Stationery Design Project for Nimbora, Chicago

Nimbora, a street parking application which helps car drivers find a street parking spot by offering an ideal path along which to look for parking. This path is calculated by our algorithm based on data (e.g. historical data, baseball games schedule, etc.). Along this path the driver will find a spot and will also save 70% of the search time. Customer we target is reg. between 21 and 45 yo.

We envision something young, fresh, bright and original. Slightly abstract maybe. It should represent the idea and elements of finding street parking in the city, e.g. car(s), parking spot, people, city, etc. (just ideas!).

Logo is attached.

Requirement:
- Business Cards (2 Sided Full Color CMYK)
- Letterhead (1 Sided Full Color CMYK)
- Envelope (1 Sided Full Color CMYK)
- Sticker (1 Sided Full Color CMYK), round with a 2inch diameter.

Reason: We're starting to get more and more designs and need more time to look into all of them. Very exciting!! Thanks to everybody!

Hi all, we're in the process of selecting our favs. Though choices!!! Really good submissions. Will keep you posted and sorry for the delay.

Target Market(s)

Car drivers and owners between 21 and 45

Industry/Entity Type

Parking

Requirements
Must have
• Sticker should be round and include company URL nimbora.com and the new logo which we will attach soon.
Should not have
• Should not be too serious or boring.

```html
<!DOCTYPE html>
<html lang="en">
<head>
<meta charset="utf-8">
<title>Nimbora Business Card</title>
<link href="https://fonts.googleapis.com/css2?family=Source+Sans+3:wght@400;600&display=swap" rel="stylesheet">
<style>
  :root {
    --page: #e4e5e7;
    --navy-dark: #1c2e66;
    --navy-mid: #1f4f86;
    --teal-blue: #236a95;
    --sphere: #1b5fd0;
    --sphere-light: #3d8af0;
    --divider-grey: #5e646b;
    --white: #ffffff;
    --name-blue: #26358c;
    --role-cyan: #27a3dc;
    --text-grey: #4a4a4a;
    --brand-dark: #2a2a2a;
    --photo-sky: #e9ecef;
    --photo-trees: #7d8c76;
    --photo-lot: #9a9ea3;
  }
  * { margin: 0; padding: 0; box-sizing: border-box; }
  html, body {
    width: 956px; height: 1200px; overflow: hidden;
    background: var(--page);
    font-family: "Source Sans 3", "Myriad Pro", sans-serif;
  }
  .card {
    position: absolute; left: 93px; width: 800px; height: 457px;
    border-radius: 26px; overflow: hidden;
    box-shadow: 0 4px 12px rgba(0,0,0,0.25);
  }
  .card-front { top: 80px; background: var(--white); }
  .card-back { top: 630px; }
  .front-art { position: absolute; inset: 0; }
  .brand-mark {
    position: absolute; left: 117px; top: 47px; width: 260px; height: 260px;
    border-radius: 50%;
    background: radial-gradient(circle at 40% 35%, var(--sphere-light), var(--sphere) 60%, var(--navy-dark));
    display: flex; align-items: center; justify-content: center;
  }
  .brand-mark-name { color: var(--white); font-size: 44px; font-weight: 600; }
  .address {
    position: absolute; left: 95px; top: 373px; width: 300px;
    color: var(--white); font-size: 20px; line-height: 27px; text-align: center;
  }
  .wordmark {
    position: absolute; right: 52px; top: 30px;
    color: var(--brand-dark); font-size: 66px; font-weight: 600; letter-spacing: 1px;
  }
  .person { position: absolute; right: 42px; top: 183px; text-align: right; }
  .person-name { color: var(--name-blue); font-size: 26px; font-weight: 600; line-height: 30px; }
  .person-role { color: var(--role-cyan); font-size: 20px; font-weight: 600; line-height: 26px; }
  .contact {
    position: absolute; right: 36px; top: 300px; list-style: none;
    text-align: right; color: var(--text-grey); font-size: 20px; line-height: 33px;
  }
  .contact b { color: var(--brand-dark); font-weight: 600; }
  .lot-photo {
    position: absolute; inset: 0;
    background:
      radial-gradient(circle at 50% 47%, rgba(255,255,255,0.9) 0, rgba(255,255,255,0.5) 170px, rgba(255,255,255,0) 300px),
      linear-gradient(180deg, var(--photo-sky) 0%, var(--photo-sky) 15%, var(--photo-trees) 24%, var(--photo-lot) 40%, #b9bcc0 100%);
  }
  .back-mark {
    position: absolute; left: 262px; top: 79px; width: 286px; height: 286px;
    border-radius: 50%;
    background: radial-gradient(circle at 40% 35%, var(--sphere-light), var(--sphere) 60%, var(--navy-dark));
    display: flex; align-items: center; justify-content: center;
  }
</style>
</head>
<body>
  <section class="card card-front">
    <svg class="front-art" width="800" height="457" viewBox="0 0 800 457" aria-hidden="true">
      <defs>
        <linearGradient id="panelBlue" x1="0" y1="0" x2="1" y2="0.3">
          <stop offset="0" stop-color="#1b2a63"/>
          <stop offset="0.5" stop-color="#1f4f86"/>
          <stop offset="1" stop-color="#236a95"/>
        </linearGradient>
      </defs>
      <path d="M0 0 H505 C470 40 455 110 490 200 C525 290 520 380 495 457 H0 Z" fill="var(--divider-grey)"/>
      <path d="M0 0 H490 C455 40 440 110 475 200 C510 290 500 380 460 457 H0 Z" fill="url(#panelBlue)"/>
    </svg>
    <div class="brand-mark"><span class="brand-mark-name">Nimbora</span></div>
    <p class="address">City Name, Street Name<br>State Name, Country Code</p>
    <div class="wordmark">nimbora</div>
    <div class="person">
      <div class="person-name">Your Name</div>
      <div class="person-role">Designation</div>
    </div>
    <ul class="contact">
      <li><b>t</b> : 123-456-7890</li>
      <li><b>c</b> : 123-456-7890</li>
      <li><b>e</b> : name@website.com</li>
      <li><b>w</b> : www.website.com</li>
    </ul>
  </section>

  <section class="card card-back">
    <div class="lot-photo" role="img" aria-label="Photo of a busy outdoor city parking lot with parked cars and trees"></div>
    <div class="back-mark"><span class="brand-mark-name">Nimbora</span></div>
  </section>
</body>
</html>
```